Cobalt Ridge Electric Needs A Logo Design

We need a logo for my new company based out of Sacramento, Ca called Cobalt Ridge Electric. The name says it all, my electrical contracting business provides "Cobalt Ridge Professional Work" I'm open to any colors that pop and customers to say Wow. I would love to print my cards on metal.

Industry/Entity Type

Business

Contact Information for Business Card

The card needs to have as follows
Name of company: Cobalt Ridge Electric
My Name: Marco Delvane
Phone # 916-555-0173
CL# 2049381
Email: cobaltridgeelectric@mailnest.example
and a slogan that represent "COBALT RIDGE"

Requirements
Must have
• The card needs to have as follows
• Name of company: Cobalt Ridge Electric
• My Name : Marco Delvane
• Phone # 916-555-0173
• CL# 2049381
• Email: cobaltridgeelectric@mailnest.example
• and a slogan that represent "COBALT RIDGE"
Nice to have
• popping colors
• electrical Arcing

```html
<!DOCTYPE html>
<html lang="en">
<head>
<meta charset="utf-8">
<title>Cobalt Ridge Electric – Business Card</title>
<link href="https://fonts.googleapis.com/css2?family=Open+Sans:wght@400;600;700&display=swap" rel="stylesheet">
<style>
  :root {
    --cobalt: #0067b1;
    --paper: #ffffff;
    --ink-light: #ffffff;
    --backdrop: #ece8e6;
  }
  * { margin: 0; padding: 0; box-sizing: border-box; }
  html, body {
    width: 1200px;
    height: 900px;
    overflow: hidden;
  }
  body {
    position: relative;
    background: var(--backdrop);
    font-family: "Open Sans", Arial, sans-serif;
  }
  .card {
    position: absolute;
    width: 556px;
    height: 343px;
  }
  .card--front {
    left: 238px;
    top: 61px;
    background: var(--cobalt);
    color: var(--ink-light);
  }
  .card--back {
    left: 457px;
    top: 518px;
    width: 560px;
    background: var(--paper);
  }
  .holder-name {
    position: absolute;
    left: 34px;
    top: 114px;
    font-size: 18px;
    font-weight: 600;
  }
  .contact-list {
    position: absolute;
    left: 34px;
    top: 160px;
    list-style: none;
    font-size: 14px;
    line-height: 20px;
  }
  .contact-list li {
    display: flex;
    align-items: center;
    gap: 8px;
  }
  .contact-list svg {
    width: 12px;
    height: 12px;
    fill: var(--ink-light);
    flex: none;
  }
  .slogan {
    position: absolute;
    left: 30px;
    top: 270px;
    font-size: 16px;
    font-weight: 600;
  }
  .front-brand {
    position: absolute;
    left: 312px;
    top: 42px;
    width: 192px;
    height: 192px;
    border: 7px solid var(--ink-light);
    border-radius: 50%;
    display: flex;
    align-items: center;
    justify-content: center;
    text-align: center;
    font-size: 22px;
    font-weight: 700;
    line-height: 1.2;
    color: var(--ink-light);
  }
  .back-brand {
    position: absolute;
    left: 0;
    right: 0;
    top: 80px;
    display: flex;
    flex-direction: column;
    align-items: center;
    gap: 18px;
  }
  .back-brand__dot {
    width: 104px;
    height: 104px;
    border-radius: 50%;
    background: var(--cobalt);
  }
  .back-brand__name {
    font-size: 34px;
    font-weight: 700;
    color: var(--cobalt);
    letter-spacing: 1px;
  }
</style>
</head>
<body>
  <section class="card card--front">
    <h1 class="holder-name">Marco Delvane</h1>
    <ul class="contact-list">
      <li>
        <svg viewBox="0 0 24 24" aria-hidden="true"><path d="M6.6 10.8a15 15 0 0 0 6.6 6.6l2.2-2.2a1 1 0 0 1 1-.25 11.4 11.4 0 0 0 3.6.57 1 1 0 0 1 1 1V20a1 1 0 0 1-1 1A17 17 0 0 1 3 4a1 1 0 0 1 1-1h3.5a1 1 0 0 1 1 1c0 1.25.2 2.45.57 3.57a1 1 0 0 1-.25 1z"/></svg>
        916-555-0173
      </li>
      <li>
        <svg viewBox="0 0 24 24" aria-hidden="true"><path d="M8 1h8a2 2 0 0 1 2 2v18a2 2 0 0 1-2 2H8a2 2 0 0 1-2-2V3a2 2 0 0 1 2-2zm0 3v14h8V4z"/></svg>
        2049381
      </li>
      <li>
        <svg viewBox="0 0 24 24" aria-hidden="true"><path d="M2 5h20v14H2zm2 2v.5l8 5 8-5V7z"/></svg>
        cobaltridgeelectric@mailnest.example
      </li>
    </ul>
    <p class="slogan">Cobalt Ridge Professional Work</p>
    <div class="front-brand">Cobalt Ridge<br>Electric</div>
  </section>

  <section class="card card--back">
    <div class="back-brand">
      <span class="back-brand__dot" aria-hidden="true"></span>
      <span class="back-brand__name">COBALT RIDGE ELECTRIC</span>
    </div>
  </section>
</body>
</html>
```